SNACKS packaging uplift

We need to revamp the current popcorn design to a new more elegant , more premium and cleaner design. The new design should have allow the consumer to immediatly relate the new pack to the old design, and not think its a totally new brand. feel free to update the logo, product shots, but we would like to maintain the WHITE identity somehow.

```html
<!DOCTYPE html>
<html lang="en">
<head>
<meta charset="utf-8">
<title>PUFFI — Tomato &amp; Herbs Popcorn Packaging</title>
<link rel="stylesheet" href="https://fonts.googleapis.com/css2?family=Patrick+Hand&family=Poppins:wght@400&display=swap">
<style>
  :root {
    --paper: #ffffff;
    --paper-shade: #f4f4f4;
    --brand-red: #d51a23;
    --deep-red: #b8141c;
    --ink: #2b2b2b;
    --ink-soft: #444444;
    --kernel: #f6ecc8;
    --tomato: #c9141c;
    --herb: #7a6a2c;
  }
  * { box-sizing: border-box; margin: 0; padding: 0; }
  html, body { width: 1200px; height: 848px; overflow: hidden; }
  body {
    position: relative;
    background: linear-gradient(180deg, var(--paper) 0%, var(--paper) 40%, var(--paper-shade) 100%);
    font-family: "Patrick Hand", cursive;
    color: var(--ink);
  }

  /* corner lockup */
  .lockup {
    position: absolute; top: 24px; left: 967px;
    display: flex; align-items: center; height: 52px;
  }
  .lockup-name {
    font-family: "Patrick Hand", cursive;
    font-size: 34px; color: var(--ink); width: 86px; line-height: 1;
  }
  .lockup-divider { width: 1px; height: 44px; background: var(--ink); margin: 0 9px 0 6px; }
  .lockup-desc {
    font-family: "Poppins", sans-serif; font-size: 12.5px; line-height: 12px; color: var(--ink);
  }

  /* main wordmark */
  .brand-block { position: absolute; left: 141px; top: 285px; width: 300px; text-align: center; }
  .brand-name {
    font-family: "Patrick Hand", cursive;
    font-size: 150px; line-height: 170px; color: var(--ink);
    letter-spacing: 2px;
  }
  .flavor-ar {
    font-family: "Patrick Hand", cursive;
    margin-top: 30px; font-size: 22px; color: var(--ink-soft); direction: rtl;
  }
  .flavor-en {
    font-size: 21px; color: var(--ink-soft); letter-spacing: 1px; white-space: nowrap;
  }

  /* backdrop disc */
  .disc {
    position: absolute; left: 665px; top: 207px;
    width: 470px; height: 470px; border-radius: 50%;
    background: var(--brand-red);
  }

  /* flat pack front */
  .pack { position: absolute; left: 528px; top: 170px; width: 369px; height: 541px; }
  .pack svg { display: block; }
  .pack-name {
    position: absolute; left: 0; width: 100%; top: 128px; text-align: center;
    font-family: "Patrick Hand", cursive; font-size: 86px; line-height: 100px; color: var(--ink);
  }
  .pack-badge {
    position: absolute; left: 48px; top: 50px; width: 64px; height: 64px; border-radius: 50%;
    background: var(--brand-red); border: 2px solid var(--ink-soft);
    color: var(--paper); font-size: 16px; line-height: 15px; text-align: center;
    display: flex; align-items: center; justify-content: center; transform: rotate(-14deg);
  }
  .pack-illustration-popcorn {
    position: absolute; left: 30px; top: 225px; width: 310px; height: 110px;
    background: radial-gradient(ellipse at center, var(--kernel) 0%, rgba(246,236,200,0) 70%);
  }
  .pack-illustration-produce {
    position: absolute; left: 92px; top: 324px; width: 170px; height: 126px; border-radius: 50%;
    background: radial-gradient(circle at 60% 40%, #e8333a 0%, var(--tomato) 55%, var(--deep-red) 100%);
  }
  .pack-copy { position: absolute; left: 0; width: 100%; top: 444px; text-align: center; color: var(--paper); }
  .pack-copy .ar { font-size: 16px; direction: rtl; line-height: 18px; }
  .pack-copy .en { font-size: 15px; letter-spacing: 0.5px; line-height: 20px; }
</style>
</head>
<body>

  <header class="lockup">
    <div class="lockup-name">PUFFI</div>
    <div class="lockup-divider"></div>
    <div class="lockup-desc">tomato &amp; herbs<br>flavored popcorn</div>
  </header>

  <section class="brand-block">
    <div class="brand-name">PUFFI</div>
    <p class="flavor-ar" lang="ar">فشار بطعم الطماطم المتبلة</p>
    <p class="flavor-en">Tomato &amp; Herbs flavored popcorn</p>
  </section>

  <div class="disc"></div>

  <article class="pack">
    <svg width="369" height="541" viewBox="0 0 369 541">
      <defs>
        <linearGradient id="packWhite" x1="0" y1="0" x2="0" y2="1">
          <stop offset="0" stop-color="#e6e6e6"/>
          <stop offset="0.12" stop-color="#ffffff"/>
          <stop offset="1" stop-color="#ffffff"/>
        </linearGradient>
        <linearGradient id="packRed" x1="0" y1="0" x2="1" y2="0">
          <stop offset="0" stop-color="#b8141c"/>
          <stop offset="0.15" stop-color="#d51a23"/>
          <stop offset="0.85" stop-color="#d51a23"/>
          <stop offset="1" stop-color="#b8141c"/>
        </linearGradient>
      </defs>
      <rect class="pack-body" x="0" y="0" width="369" height="541" fill="url(#packWhite)"/>
      <path class="pack-band" d="M0 282 L34 285 L84 335 L139 285 L186 335 L238 285 L288 335 L343 300 L369 298 L369 541 L0 541 Z" fill="url(#packRed)"/>
      <path d="M30 150 Q60 120 90 108" fill="none" stroke="#666" stroke-width="2"/>
      <path d="M28 162 Q64 132 98 118" fill="none" stroke="#666" stroke-width="2"/>
    </svg>
    <div class="pack-illustration-popcorn" role="img" aria-label="Illustration of scattered popped popcorn kernels"></div>
    <div class="pack-badge">Air<br>poped!</div>
    <div class="pack-name">PUFFI</div>
    <div class="pack-illustration-produce" role="img" aria-label="Illustration of a whole tomato, a sliced tomato and a spoon of dried herbs"></div>
    <div class="pack-copy">
      <p class="ar" lang="ar">فشار بطعم الطماطم المتبلة</p>
      <p class="en">Tomato &amp; Herbs flavored popcorn</p>
    </div>
  </article>

</body>
</html>
```